Boutique custom software development company needs new business card

Our nearly 20 year old custom software development company would like to better include the fact that we are now providing Bitcoin services. These new services are B2B include education (how to acquire and securely hold Bitcoin) and integrating Bitcoin payments into existing ecommerce sites or other existing systems. Please keep the card clean and simple. Attached is our current design and some other files. vextorial.com

Target Market(s)

businesses owners interested in long term relationship

Industry/Entity Type

Custom software development and Bitcoin

Contact Information for Business Card

Dale Parker, dale@vextorial.com, vextorial.com, (888) 555-VXTRL

Font styles to use
Other font styles liked:
• monospace

Requirements
Must have
• double-sided
Nice to have
• clean and simple
Should not have
• physical address

```html
<!DOCTYPE html>
<html lang="en">
<head>
<meta charset="utf-8">
<title>Vextorial business card</title>
<link href="https://fonts.googleapis.com/css2?family=Roboto+Mono:wght@400;500;700&family=Lato:wght@400&display=swap" rel="stylesheet">
<style>
  :root {
    --blue: #3f72b8;
    --orange: #ef7b22;
    --ink: #2b2b2b;
    --card: #ffffff;
    --backdrop: #e7e4df;
    --faint: #f1f4f9;
  }
  * { margin: 0; padding: 0; box-sizing: border-box; }
  html, body { width: 900px; height: 1200px; overflow: hidden; }
  body { background: var(--backdrop); position: relative; font-family: "Roboto Mono", monospace; color: var(--ink); }

  .card { position: absolute; left: 78px; width: 744px; height: 442px; background: var(--card); box-shadow: 0 6px 18px rgba(0,0,0,.18); }
  .card-front { top: 130px; }
  .card-back { top: 637px; height: 441px; }

  .brand-name { position: absolute; left: 26px; top: 28px; font-family: "Roboto Mono", monospace; font-weight: 700; font-size: 58px; line-height: 1; color: var(--blue); letter-spacing: -1px; }
  .tagline { position: absolute; left: 40px; top: 104px; font-family: "Lato", sans-serif; font-size: 22px; color: var(--blue); letter-spacing: -0.5px; }

  .services { position: absolute; left: 26px; top: 200px; list-style: none; font-size: 16px; line-height: 25px; }

  .contact-list { position: absolute; left: 26px; top: 345px; list-style: none; font-size: 16px; line-height: 25px; }
  .contact-list li { display: flex; align-items: center; gap: 8px; }
  .contact-list svg { width: 17px; height: 17px; fill: var(--orange); flex: none; }

  .mark-faint { position: absolute; left: 515px; top: 116px; width: 204px; height: 212px; background: var(--faint); }

  .person { position: absolute; right: 26px; top: 190px; text-align: right; }
  .person-name { font-size: 29px; font-weight: 500; color: var(--orange); line-height: 36px; }
  .person-role { font-size: 16px; line-height: 24px; }
  .accent-bar { position: absolute; right: 0; top: 195px; width: 16px; height: 52px; background: var(--orange); }

  .back-mark { position: absolute; left: 220px; top: 63px; width: 306px; height: 318px; background: var(--blue); display: flex; align-items: center; justify-content: center; }
  .back-mark-name { font-family: "Roboto Mono", monospace; font-weight: 700; font-size: 38px; color: #ffffff; letter-spacing: -1px; }
</style>
</head>
<body>
  <section class="card card-front">
    <div class="brand-name">VEXTORIAL</div>
    <div class="tagline">developer of custom applications</div>

    <div class="mark-faint"></div>

    <ul class="services">
      <li>Custom Software</li>
      <li>Bitcoin Education</li>
      <li>Bitcoin Payments</li>
    </ul>

    <div class="person">
      <div class="person-name">Dale Parker</div>
      <div class="person-role">Founding Partner</div>
    </div>
    <div class="accent-bar"></div>

    <ul class="contact-list">
      <li>
        <svg viewBox="0 0 24 24" aria-hidden="true"><path d="M3 8c0-3 4-5 9-5s9 2 9 5v2h-5V8c-1-1-7-1-8 0v2H3zM6 12h12l2 8H4z"/></svg>
        (888) 555-VXTRL
      </li>
      <li>
        <svg viewBox="0 0 24 24" aria-hidden="true"><path d="M2 5h20v2l-10 6L2 7zM2 9l10 6 10-6v10H2z"/></svg>
        dale@vextorial.com
      </li>
      <li>
        <svg viewBox="0 0 24 24" aria-hidden="true"><path d="M12 2a10 10 0 1 0 0 20 10 10 0 0 0 0-20zm-1 3 2 2-2 3 3 2 1 4-3 3-1-4-3-2-2-3 2-4z"/></svg>
        www.vextorial.com
      </li>
    </ul>
  </section>

  <section class="card card-back">
    <div class="back-mark"><span class="back-mark-name">VEXTORIAL</span></div>
  </section>
</body>
</html>
```